Business card alterations

I have changed my business name from Brisa Laser Renewal Clinic to simply "Brisa Laser Clinic' and need this logo changed to reflect same

Brisa Laser Clinic
Est. 2004

I also need new business cards with above logo included and this attached card changed to the following.
Marianne Holcroft
Dermal Aesthetician
Grad Cert in Laser & IPL Treatments

I need at least one logo in less than 4mb so I can upload into my newsletter format so I can upload to newsletters, emails etc

Thanks
Mari

```html
<!DOCTYPE html>
<html lang="en">
<head>
<meta charset="utf-8">
<title>Brisa Laser Clinic – Business Card</title>
<link rel="stylesheet" href="https://fonts.googleapis.com/css2?family=Lato:wght@400;700&display=swap">
<style>
  :root {
    --card-green: #00a05a;
    --band-white: #ffffff;
    --text-white: #ffffff;
    --text-green: #00a05a;
    --backdrop: #e9e9ea;
  }
  * { box-sizing: border-box; margin: 0; padding: 0; }
  html, body {
    width: 1200px;
    height: 864px;
    overflow: hidden;
    background: var(--backdrop);
    font-family: "Lato", sans-serif;
  }
  .canvas {
    position: relative;
    width: 1200px;
    height: 864px;
    display: flex;
    align-items: center;
    justify-content: center;
  }
  .business-card {
    position: relative;
    width: 900px;
    height: 550px;
    background: var(--card-green);
    color: var(--text-white);
    text-align: center;
    box-shadow: 0 18px 40px rgba(0,0,0,0.18);
    overflow: hidden;
  }
  .brand-wordmark {
    position: absolute;
    top: 28px;
    left: 0;
    right: 0;
    font-size: 118px;
    font-weight: 400;
    line-height: 1;
    letter-spacing: 2px;
  }
  .clinic-name {
    position: absolute;
    top: 172px;
    left: 0;
    right: 0;
    font-size: 34px;
    font-weight: 700;
    letter-spacing: 6px;
  }
  .established {
    position: absolute;
    top: 216px;
    left: 0;
    right: 0;
    font-size: 20px;
    letter-spacing: 5px;
  }
  .qualification {
    position: absolute;
    top: 248px;
    left: 0;
    right: 0;
    font-size: 19px;
  }
  .person-name {
    position: absolute;
    top: 300px;
    left: 0;
    right: 0;
    font-size: 27px;
  }
  .person-role {
    position: absolute;
    top: 338px;
    left: 0;
    right: 0;
    font-size: 19px;
  }
  .contact-band {
    position: absolute;
    top: 392px;
    left: 0;
    right: 0;
    height: 66px;
    background: var(--band-white);
    color: var(--text-green);
    display: flex;
    align-items: center;
    justify-content: center;
    gap: 22px;
    font-size: 22px;
  }
  .contact-band .divider { font-size: 28px; }
  .address {
    position: absolute;
    top: 476px;
    left: 0;
    right: 0;
    font-size: 22px;
  }
  .bottom-rule {
    position: absolute;
    bottom: 14px;
    left: 0;
    right: 0;
    height: 6px;
    background: var(--band-white);
  }
</style>
</head>
<body>
  <main class="canvas">
    <article class="business-card">
      <div class="brand-wordmark">Brisa</div>
      <div class="clinic-name">Brisa Laser Clinic</div>
      <div class="established">Est. 2004</div>
      <div class="qualification">Grad Cert in Laser &amp; IPL Treatments</div>
      <div class="person-name">Marianne Holcroft</div>
      <div class="person-role">Dermal Aesthetician</div>
      <div class="contact-band">
        <span class="phone">(08) 8412 5790</span>
        <span class="divider">/</span>
        <span class="email">info@brisaclinic.com.au</span>
        <span class="divider">/</span>
        <span class="website">www.brisaclinic.com.au</span>
      </div>
      <div class="address">214 Marlow Avenue Kensington SA 5068</div>
      <div class="bottom-rule"></div>
    </article>
  </main>
</body>
</html>
```